FinTech company looking to revamp and expand client-facing interface for our financial models

Pellworth Engines currently has a very simple website that allows clients to interact with our financial models. We are looking to completely redesign the current site and add several extra pages to provide extra functionality. We want the design to have a modern, slick feel, that will work on both a desktop or a tablet. It should be straightforward for clients to move between different pages at any time, and clear from the layout how to interact with the more advanced features. We have included screenshots of existing pages in the attached design brief, as well as sketches of the functionality required by the new pages, but can't provide a direct link to the current site.
Target Market(s)
Professional investors that will be paying to access the interface
Industry/Entity Type
Finance
Number of Pages Required
4 page
Colors
Designer to choose colors to be used in the design.
Look and feel
Each slider illustrates characteristics of the customer's brand and the style your logo design should communicate.

```html
<!DOCTYPE html>
<html lang="en">
<head>
<meta charset="utf-8">
<title>QSTACK – Models · Pellworth Engines</title>
<link rel="stylesheet" href="https://fonts.googleapis.com/css2?family=Open+Sans:wght@400;600;700&family=Roboto+Condensed:wght@400;500&display=swap">
<style>
  :root {
    --page-bg: #e6e6e6;
    --panel-top: #d8d8d8;
    --panel-bottom: #f7f7f7;
    --white: #ffffff;
    --ink: #111111;
    --nav-active: #333333;
    --nav-divider: #e3e3e3;
    --navy: #003366;
    --grey-head: #666666;
    --row-alt: #f3f3f3;
    --cell-line: #e4e4e4;
    --link-blue: #1f4f9a;
    --input-line: #dcdcdc;
  }
  * { box-sizing: border-box; margin: 0; padding: 0; }
  html, body { width: 1200px; height: 618px; overflow: hidden; }
  body {
    background: var(--page-bg);
    font-family: "Open Sans", Arial, sans-serif;
    color: var(--ink);
    position: relative;
  }
  .app {
    position: absolute; left: 14px; top: 14px;
    width: 1172px; height: 590px;
    background: linear-gradient(180deg, var(--panel-top) 55px, #ececec 160px, var(--panel-bottom) 100%);
  }
  .topbar {
    position: absolute; left: 0; top: 0; width: 1172px; height: 55px;
    background: var(--white); display: flex; align-items: stretch;
  }
  .brand {
    width: 166px; padding-left: 53px; display: flex; align-items: center;
    font-weight: 700; font-size: 16px; letter-spacing: 0.2px;
  }
  .horizon-tabs { display: flex; }
  .horizon-tab {
    width: 83px; display: flex; align-items: center; justify-content: center;
    font-weight: 700; font-size: 13px; border-right: 1px solid var(--nav-divider);
  }
  .horizon-tab.active { background: var(--nav-active); color: var(--white); border-right: none; }
  .page-nav { margin-left: auto; display: flex; margin-right: 0; }
  .page-link {
    display: flex; align-items: center; justify-content: center; gap: 7px;
    font-weight: 700; font-size: 12.5px; border-left: 1px solid var(--nav-divider);
  }
  .page-link svg { width: 22px; height: 22px; }
  .page-link.models { width: 130px; background: var(--nav-active); color: var(--white); border-left: none; }
  .page-link.sensitivities { width: 163px; }
  .page-link.favourites { width: 154px; margin-right: 14px; }

  .filters {
    position: absolute; left: 53px; top: 106px; width: 1068px; height: 28px;
    display: flex; align-items: center; font-size: 15px;
  }
  .filter-label strong { font-weight: 700; }
  .filter-label .gap { display: inline-block; width: 22px; }
  .filter-input {
    height: 28px; width: 166px; background: var(--white);
    border: 1px solid var(--input-line); border-radius: 3px;
    padding-left: 12px; display: flex; align-items: center; font-size: 15px;
    margin-left: 12px;
  }
  .filter-group + .filter-group { margin-left: 38px; }
  .filter-group { display: flex; align-items: center; }
  .export {
    margin-left: auto; display: flex; align-items: center; gap: 6px;
    color: var(--link-blue); font-weight: 700; font-size: 15px;
  }
  .export svg { width: 24px; height: 22px; }

  .models-table {
    position: absolute; left: 51px; top: 157px; width: 1070px;
    border-collapse: separate; border-spacing: 0; table-layout: fixed;
    border-radius: 6px; overflow: hidden;
    box-shadow: 0 2px 8px rgba(0,0,0,0.12);
    font-family: "Roboto Condensed", "Arial Narrow", sans-serif;
  }
  .models-table th {
    height: 65px; color: var(--white); font-family: "Open Sans", Arial, sans-serif;
    font-weight: 600; font-size: 16px; text-align: center;
    background: var(--grey-head); border-right: 1px solid #777;
  }
  .models-table th.key { background: var(--navy); border-right: 1px solid #1a4a7a; }
  .models-table th:last-child { border-right: none; }
  .models-table th svg { width: 10px; height: 7px; margin-left: 5px; vertical-align: middle; }
  .models-table td {
    height: 64.6px; font-size: 15.5px; padding: 0 9px; line-height: 19px;
    background: var(--white); border-right: 1px solid var(--cell-line);
  }
  .models-table td:last-child { border-right: none; }
  .models-table tr:nth-child(even) td { background: var(--row-alt); }
  .models-table td.id { text-align: center; }
  .models-table td.time { text-align: center; padding: 0 6px; }
  .models-table td.quality { text-align: center; }
</style>
</head>
<body>
<div class="app">
  <header class="topbar">
    <div class="brand">QSTACK</div>
    <nav class="horizon-tabs">
      <div class="horizon-tab active">250D</div>
      <div class="horizon-tab">83D</div>
      <div class="horizon-tab">42D</div>
    </nav>
    <nav class="page-nav">
      <div class="page-link models">
        <svg viewBox="0 0 24 24" fill="none" stroke="currentColor" stroke-width="2"><path d="M3 11 12 3l9 8"/><path d="M5 10v11h5v-6h4v6h5V10"/></svg>
        MODELS
      </div>
      <div class="page-link sensitivities">
        <svg viewBox="0 0 24 24" fill="none" stroke="currentColor" stroke-width="1.6"><circle cx="12" cy="12" r="4"/><circle cx="12" cy="12" r="8" stroke-dasharray="2 2"/><circle cx="12" cy="12" r="10.5" stroke-dasharray="1.5 2.5"/></svg>
        SENSITIVITIES
      </div>
      <div class="page-link favourites">
        <svg viewBox="0 0 24 24" fill="none" stroke="currentColor" stroke-width="1.8" stroke-linejoin="round"><path d="M12 2.5l2.9 6.2 6.6.7-5 4.5 1.4 6.6L12 17.2l-5.9 3.3 1.4-6.6-5-4.5 6.6-.7z"/></svg>
        FAVOURITES
      </div>
    </nav>
  </header>

  <section class="filters">
    <div class="filter-group">
      <span class="filter-label">Quality<span class="gap"></span><strong>Threshold:</strong></span>
      <div class="filter-input">-10</div>
    </div>
    <div class="filter-group">
      <span class="filter-label"><strong>Abs.</strong> Stat&nbsp;&nbsp; <strong>Threshold:</strong></span>
      <div class="filter-input">-10</div>
    </div>
    <div class="export">
      <svg viewBox="0 0 24 22" fill="none" stroke="currentColor" stroke-width="2.2" stroke-linecap="round" stroke-linejoin="round"><path d="M10 5H5a2 2 0 0 0-2 2v10a2 2 0 0 0 2 2h11a2 2 0 0 0 2-2v-4"/><path d="M9 14c1-5 5-8 11-8"/><path d="M16 2.5l4 3.5-4 3.5"/></svg>
      Export
    </div>
  </section>

  <table class="models-table">
    <colgroup>
      <col style="width:92px"><col style="width:102px"><col style="width:106px"><col style="width:106px">
      <col style="width:83px"><col style="width:83px"><col style="width:83px"><col style="width:83px">
      <col style="width:83px"><col style="width:83px"><col style="width:83px"><col style="width:83px">
    </colgroup>
    <thead>
      <tr>
        <th class="key">ID<svg viewBox="0 0 10 7" fill="none" stroke="currentColor" stroke-width="2"><path d="M1 1l4 4 4-4"/></svg></th>
        <th class="key">Sector</th>
        <th class="key">Time</th>
        <th>Quality</th>
        <th>Stat 1</th><th>Stat 2</th><th>Stat 3</th><th>Stat 4</th>
        <th>Stat 5</th><th>Stat 6</th><th>Stat 7</th><th>Stat 8</th>
      </tr>
    </thead>
    <tbody>
      <tr>
        <td class="id">Model 1</td><td>Materials</td>
        <td class="time">2019-07-03<br>12:15:00.000</td><td class="quality">30.2288</td>
        <td>2.01574</td><td>23.305</td><td>-0.149368</td><td>22.3054</td>
        <td>4.63714</td><td>0.945706</td><td>2.81949</td><td>2.60858</td>
      </tr>
      <tr>
        <td class="id">Model 2</td><td>Industrials</td>
        <td class="time">2019-07-03<br>12:15:00.000</td><td class="quality">32.8694</td>
        <td>0.87307</td><td>32.185</td><td>-0.033692</td><td>33.9911</td>
        <td>11.5693</td><td>-0.472968</td><td>-0.830458</td><td>6.80646</td>
      </tr>
      <tr>
        <td class="id">Model 3</td><td>Consumer<br>Discretionary</td>
        <td class="time">2019-07-03<br>12:15:00.000</td><td class="quality">1.66002</td>
        <td>-0.569222</td><td>159.814</td><td>0.0252328</td><td>172.616</td>
        <td>10.2875</td><td>-0.750396</td><td>-0.385309</td><td>4.69146</td>
      </tr>
      <tr>
        <td class="id">Model 4</td><td>Information<br>Technology</td>
        <td class="time">2019-07-03<br>12:15:00.000</td><td class="quality">45.6856</td>
        <td>0.412148</td><td>202.488</td><td>0.0084923</td><td>205.834</td>
        <td>11.9094</td><td>-0.137913</td><td>0.449595</td><td>3.85106</td>
      </tr>
      <tr>
        <td class="id">Model 5</td><td>Information<br>Technology</td>
        <td class="time">2019-07-03<br>12:15:00.000</td><td class="quality">75.7733</td>
        <td>7.06728</td><td>188.605</td><td>0.016913</td><td>161.665</td>
        <td>3.82241</td><td>0.981019</td><td>1.29847</td><td>3.34927</td>
      </tr>
    </tbody>
  </table>
</div>
</body>
</html>
```